Marlow Vale Stud website

We would like to create a horse stud/agistment farm website similar to this websites we have attached below:
www.thornbeck.com.au
www.quillstead.com.au
www.brackley.com
www.pimsey.com.au
The main colour scheme are purple and white to align with the stable's racing colours.
We have also attach the company logo and also images of the farm and create some ideas for the website.
Many thanks for looking into this project!

```html
<!DOCTYPE html>
<html lang="en">
<head>
<meta charset="utf-8">
<title>Marlow Vale Stud</title>
<link rel="stylesheet" href="https://fonts.googleapis.com/css2?family=Cinzel:wght@400;700&family=Marcellus&family=Lato:wght@400;700&display=swap">
<style>
:root{
  --plum:#3b1a40;
  --plum-deep:#2b0f30;
  --plum-mid:#4d2453;
  --ink:#2b2b2b;
  --muted:#7a7a7a;
  --line:#e2e2e2;
  --white:#ffffff;
  --ghost:#f1f1f1;
}
*{box-sizing:border-box;margin:0;padding:0}
html,body{width:1200px;height:4036px;overflow:hidden;background:var(--white)}
body{font-family:"Lato",Arial,sans-serif;color:var(--ink)}
.page{position:relative;width:1200px;height:4036px;overflow:hidden}
.abs{position:absolute}
.photo{position:absolute}

/* header */
.site-header{position:absolute;left:0;top:0;width:1200px;height:89px;background:var(--plum-deep);border-bottom:2px solid #6d4a72}
.brand{position:absolute;left:145px;top:27px;font-family:"Cinzel",Georgia,serif;font-size:26px;color:var(--white);white-space:nowrap}
.main-nav{position:absolute;right:180px;top:34px;display:flex;gap:24px;font-size:15px;color:var(--white);white-space:nowrap}
.search-icon{position:absolute;left:1038px;top:34px}

/* hero */
.hero{left:0;top:89px;width:1200px;height:691px;background:linear-gradient(180deg,#5e8fc9 0%,#9cc0e6 35%,#dfe9f1 55%,#4f3a2a 70%,#3f6b2e 85%,#5d8f3c 100%)}
.slide-arrow{position:absolute;width:40px;height:40px;border-radius:50%;background:#111;top:413px}
.hero-title{position:absolute;left:145px;top:490px;width:565px;height:76px;background:rgba(20,20,20,.72);padding-left:50px;font-family:"Cinzel",Georgia,serif;font-size:46px;line-height:76px;color:var(--white);white-space:nowrap;overflow:hidden}
.hero-sub{position:absolute;left:145px;top:568px;width:565px;height:44px;background:linear-gradient(90deg,rgba(59,26,64,.75),rgba(59,26,64,0));padding-left:55px;line-height:44px;font-size:17px;color:var(--white);white-space:nowrap}
.dots{position:absolute;left:553px;top:716px;display:flex;gap:6px}
.dots span{width:13px;height:13px;border-radius:50%;border:2px solid var(--white)}
.dots span.on{background:var(--white)}

/* news */
.ghost-word{position:absolute;font-family:"Lato",Arial,sans-serif;font-weight:700;color:var(--ghost);white-space:nowrap;line-height:1}
.section-title{position:absolute;font-family:"Cinzel",Georgia,serif;font-size:32px;color:var(--plum);display:flex;align-items:center;gap:10px;white-space:nowrap}
.section-title i{display:inline-block;width:20px;height:20px;border-radius:50%;background:currentColor}
.news-card{position:absolute;top:1215px;width:432px;height:410px;border:1px solid var(--line);background:var(--white)}
.news-card .photo{left:14px;top:0;width:402px;height:215px;border-radius:10px 10px 0 0}
.badge{position:absolute;left:330px;top:190px;width:56px;height:56px;border-radius:50%;background:var(--white);box-shadow:0 1px 4px rgba(0,0,0,.2)}
.news-card h3{position:absolute;left:22px;top:252px;font-size:18px;font-weight:400;color:var(--ink)}
.news-card p{position:absolute;left:22px;top:288px;width:390px;font-size:12px;line-height:22px;color:var(--muted)}
.meta{position:absolute;left:22px;top:352px;font-size:12px;color:#444;display:flex;gap:16px;align-items:center}
.meta span{display:flex;align-items:center;gap:5px}
.round-arrow{position:absolute;width:46px;height:46px;border-radius:50%;border:1px solid #444;background:var(--white)}

/* about */
.about-band{position:absolute;left:0;top:1716px}
.about-title{left:575px;top:1828px;color:var(--white)}
.about-text{position:absolute;left:575px;top:1892px;width:470px;font-size:13px;line-height:31px;color:var(--white)}
.btn-outline{position:absolute;left:575px;top:2088px;width:142px;height:42px;border:2px solid var(--white);border-radius:21px;color:var(--white);font-size:13px;text-align:center;line-height:38px;font-family:"Cinzel",Georgia,serif}

/* history */
.year{position:absolute;font-family:"Cinzel",Georgia,serif;font-weight:700;font-size:82px;color:var(--ink);line-height:1;z-index:2}
.history-caption{position:absolute;top:2815px;height:56px;background:var(--white);box-shadow:0 3px 10px rgba(0,0,0,.18);font-family:"Marcellus",Georgia,serif;font-size:21px;text-align:center;line-height:56px;color:var(--ink)}
.label-2019{position:absolute;left:948px;top:2752px;width:252px;height:53px;background:var(--plum);clip-path:polygon(4% 0,100% 0,100% 100%,0 100%);color:var(--white);font-size:22px;line-height:53px;padding-left:64px;font-family:"Marcellus",Georgia,serif;z-index:2}

/* newsletter */
.newsletter{left:0;top:3013px;width:1200px;height:470px;background:linear-gradient(180deg,#2d2c34 0%,#6b6a73 30%,#b9a98e 48%,#6f7440 66%,#4a5a2a 82%,#3b4a22 100%)}
.news-title{position:absolute;left:145px;top:3180px;font-family:"Cinzel",Georgia,serif;font-weight:700;font-size:44px;color:var(--white);display:flex;align-items:center;gap:12px;white-space:nowrap}
.news-title i{width:24px;height:24px;border-radius:50%;background:var(--white);display:inline-block}
.news-sub{position:absolute;left:190px;top:3250px;font-size:17px;color:var(--white)}
.field{position:absolute;top:3308px;height:47px;width:272px;background:var(--white);font-size:14px;color:#666;padding-left:20px;line-height:47px}
.btn-sign{position:absolute;left:752px;top:3308px;width:110px;height:47px;background:var(--plum);color:var(--white);font-size:14px;text-align:center;line-height:47px}

/* gallery */
.tile{position:absolute;top:3492px;height:188px}
.tile-text{background:var(--plum);color:var(--white);text-align:center;font-size:12px;line-height:20px;padding-top:58px}

/* footer */
.stay{left:145px;top:3762px;color:var(--plum)}
.social{position:absolute;top:3825px;width:40px;height:40px;border-radius:50%}
.footer-brand{position:absolute;left:450px;top:3790px;width:160px;text-align:center;font-family:"Cinzel",Georgia,serif;font-size:26px;line-height:34px;color:var(--plum)}
.links h4{font-family:"Cinzel",Georgia,serif;font-weight:400;font-size:21px;color:var(--ink);margin-bottom:14px}
.links ul{list-style:none;font-size:13px;color:#333}
.links li{line-height:29px;padding-left:20px;position:relative}
.links li::before{content:"";position:absolute;left:3px;top:11px;border-left:6px solid #555;border-top:4px solid transparent;border-bottom:4px solid transparent}
.bottom-bar{position:absolute;left:0;top:3976px;width:1200px;height:60px;background:var(--plum-deep);color:var(--white);font-size:12px;text-align:center;line-height:60px}
</style>
</head>
<body>
<div class="page">

  <header class="site-header">
    <div class="brand">Marlow Vale Stud</div>
    <nav class="main-nav"><span>Home</span><span>About us</span><span>News</span><span>Horses for sale</span><span>Videos</span><span>Contact us</span></nav>
    <svg class="search-icon" width="18" height="18" viewBox="0 0 18 18"><circle cx="7.5" cy="7.5" r="5.5" fill="none" stroke="#fff" stroke-width="2.4"/><line x1="11.5" y1="11.5" x2="16.5" y2="16.5" stroke="#fff" stroke-width="2.6"/></svg>
  </header>

  <div class="photo hero" role="img" aria-label="Five dark bay horses standing on green pasture under a blue sky"></div>
  <div class="slide-arrow" style="left:52px"><svg width="40" height="40" viewBox="0 0 40 40"><path d="M23 13l-7 7 7 7" fill="none" stroke="#fff" stroke-width="2.5"/></svg></div>
  <div class="slide-arrow" style="left:1107px"><svg width="40" height="40" viewBox="0 0 40 40"><path d="M17 13l7 7-7 7" fill="none" stroke="#fff" stroke-width="2.5"/></svg></div>
  <div class="hero-title">Marlow Vale Stud</div>
  <div class="hero-sub">Lorem ipsum dolor sit ametconsectetur adipiscing elit</div>
  <div class="dots"><span></span><span></span><span class="on"></span><span></span><span></span></div>

  <div class="photo" style="left:16px;top:793px;width:341px;height:229px;background:linear-gradient(180deg,#3f5a2a,#6c8f3d 55%,#8aa94f)" role="img" aria-label="Chestnut horse grazing in a paddock"></div>
  <div class="photo" style="left:373px;top:793px;width:340px;height:229px;background:linear-gradient(160deg,#4c6a34,#c8b89a 55%,#8c9c5a)" role="img" aria-label="Palomino horse close up"></div>
  <div class="photo" style="left:730px;top:793px;width:340px;height:229px;background:linear-gradient(180deg,#6a8f4a,#5a3a22 50%,#86b04a)" role="img" aria-label="Bay horse standing by a fence"></div>
  <div class="photo" style="left:1086px;top:793px;width:114px;height:229px;background:linear-gradient(180deg,#3c4a2a,#6b7d3e)" role="img" aria-label="Horse in a shaded paddock"></div>

  <div class="ghost-word" style="left:203px;top:1075px;font-size:118px">LATEST NEWS</div>
  <div class="section-title" style="left:477px;top:1112px"><i></i>LATEST NEWS</div>

  <article class="news-card" style="left:145px">
    <div class="photo" style="background:linear-gradient(180deg,#0e1a22,#6b5a6e 50%,#2f7a3a)" role="img" aria-label="Jockey in purple silks riding a grey horse at the track"></div>
    <div class="badge"></div>
    <h3>Lorem ipsum dolor sit amet</h3>
    <p>Sed ut perspiciatis unde omnis iste natus error sit voluptatem accusantium doloremque laudantium rem aperiam</p>
    <div class="meta"><span>▦ March 15,2019</span><span>♡ 2</span><span>◌ 4</span></div>
  </article>
  <article class="news-card" style="left:623px">
    <div class="photo" style="background:linear-gradient(180deg,#4a2a22,#8a5a3a 40%,#d9d2c4 65%,#c84a6a)" role="img" aria-label="Jockey in purple silks racing a grey horse past flowers"></div>
    <div class="badge"></div>
    <h3>Lorem ipsum dolor sit amet</h3>
    <p>Sed ut perspiciatis unde omnis iste natus error sit voluptatem accusantium doloremque laudantium rem aperiam</p>
    <div class="meta"><span>▦ March 15,2019</span><span>♡ 2</span><span>◌ 4</span></div>
  </article>
  <div class="round-arrow" style="left:62px;top:1395px"><svg width="44" height="44" viewBox="0 0 44 44"><path d="M25 15l-7 7 7 7" fill="none" stroke="#222" stroke-width="2.5"/></svg></div>
  <div class="round-arrow" style="left:1090px;top:1395px"><svg width="44" height="44" viewBox="0 0 44 44"><path d="M19 15l7 7-7 7" fill="none" stroke="#222" stroke-width="2.5"/></svg></div>

  <svg class="about-band" width="1200" height="530" viewBox="0 0 1200 530"><polygon points="0,0 1200,60 1200,440 0,530" fill="#3b1a40"/></svg>
  <div class="ghost-word" style="left:880px;top:2040px;font-size:118px;color:rgba(255,255,255,.05)">ABOUT</div>
  <div class="photo" style="left:168px;top:1775px;width:330px;height:410px;border-radius:165px 165px 40px 40px;background:linear-gradient(180deg,#5b5a66,#3f4c3a 45%,#8a4a7a 70%,#4e6a30)" role="img" aria-label="Stable courtyard with flower beds"></div>
  <div class="section-title about-title"><i></i>ABOUT US</div>
  <p class="about-text">Lorem ipsum dolor sit amet, consectetur adipiscing elit, sed do eiusmod tempor incididunt ut labore et dolore magna aliqua ut enim ad minim veniam, quis nostrud exercitation ullamco laboris nisi ut aliquip commodo consequat aute irure dolor in reprehenderit in voluptate velit esse cillum dolore eu fugiat nulla pariatur sint occaecat laborum</p>
  <div class="btn-outline">READ MORE</div>

  <div class="ghost-word" style="left:0;top:2290px;font-size:118px">OUR HISTORY</div>
  <div class="section-title" style="left:145px;top:2372px;color:var(--ink)"><i></i>EXPLORE OUR HISTORY</div>
  <div class="photo" style="left:825px;top:2400px;width:300px;height:545px;border-radius:45% 35% 20% 30%;background:radial-gradient(ellipse at 50% 45%,#8a4a24,#6a3318 60%,rgba(255,255,255,0) 72%)" role="img" aria-label="Chestnut horse standing, cut out on white"></div>
  <div class="year" style="left:140px;top:2495px">1990</div>
  <div class="year" style="left:572px;top:2495px">2010</div>
  <div class="year" style="left:995px;top:2370px;color:var(--plum)">2019</div>
  <div class="photo" style="left:143px;top:2590px;width:314px;height:222px;background:linear-gradient(180deg,#2e3a22,#cbb893 50%,#6a9a3a)" role="img" aria-label="Palomino horse in a green paddock"></div>
  <div class="photo" style="left:488px;top:2590px;width:315px;height:218px;background:linear-gradient(180deg,#2c3b24,#6b3d22 50%,#5f9232)" role="img" aria-label="Bay horse in a green paddock"></div>
  <div class="history-caption" style="left:143px;width:314px">Voccaecati cupiditat</div>
  <div class="history-caption" style="left:488px;top:2810px;width:315px">Voccaecati cupiditat</div>
  <div class="label-2019">Vocca piditat</div>

  <div class="photo newsletter" role="img" aria-label="Farm paddocks and fences at sunset"></div>
  <div class="news-title"><i></i>SIGN UP NEWSLETTER</div>
  <div class="news-sub">At vero eos et accusamdio dignissimos ducimus qui blanditiis</div>
  <div class="field" style="left:190px">Enter Name</div>
  <div class="field" style="left:470px">Email Address</div>
  <div class="btn-sign">SIGN UP</div>

  <div class="photo tile" style="left:12px;width:281px;background:linear-gradient(180deg,#6a7a86,#8a8a52 40%,#7a6a3a)" role="img" aria-label="Horse resting in an open field"></div>
  <div class="tile tile-text" style="left:310px;width:280px">Lorem ipsum dolor sit amet,<br>consectetur adipiscing.<div style="font-size:15px;margin-top:10px">♡ 2 &nbsp; ◌ 4</div></div>
  <div class="photo tile" style="left:608px;width:282px;background:linear-gradient(180deg,#4a7a3a,#8ab05a 50%,#5a8a3a)" role="img" aria-label="Aerial view of paddocks and stables"></div>
  <div class="photo tile" style="left:906px;width:282px;background:linear-gradient(180deg,#5a8a42,#9aa86a 50%,#6a8a4a)" role="img" aria-label="Aerial view of barns and yards"></div>

  <div class="section-title stay">STAY IN TOUCH</div>
  <div class="social" style="left:145px;background:#1f3f8a"></div>
  <div class="social" style="left:198px;background:#3aa6e8"></div>
  <div class="social" style="left:252px;background:#1a6aa8"></div>
  <div class="social" style="left:306px;background:#c81e1e"></div>
  <div class="footer-brand">Marlow Vale Stud</div>
  <div class="links abs" style="left:680px;top:3745px"><h4>QUICK LINKS</h4><ul><li>Home</li><li>About us</li><li>News</li><li>Horses for sale</li><li>Videos</li><li>Contact us</li></ul></div>
  <div class="links abs" style="left:922px;top:3745px"><h4>OTHER LINKS</h4><ul><li>Privacy policy</li><li>Terms and use</li><li>Information</li><li>Sitemap</li><li>Events</li></ul></div>

  <footer class="bottom-bar">Copyright 2019 © Companyname.All Rights Reserved &nbsp;|&nbsp; Privacy policy</footer>
</div>
</body>
</html>
```